Makers' Hollow - Landing page for small and large screen

Makers’ Hollow gives you the space you need to take your side project from idea to reality.

With three days of focused work, it’s a place for you iron out the details of your business idea away from the distractions of the city.

The full copy and structure is here:
https://www.makershollow.co.uk/landing

What it needs, a touch of colour.

Target Market(s)

25-35 working in digital industry, software developer, a UI or UX designer

Number of Pages Required

1 page

Font styles to use
Sans Serif

Colors
0292cd
33b8a4
86cfc6
fdf9cf
ec1f27

Requirements
Should not have
• gradients or too much images

```html
<!DOCTYPE html>
<html lang="en">
<head>
<meta charset="utf-8">
<title>Makers' Hollow – focus. build. launch.</title>
<link rel="stylesheet" href="https://fonts.googleapis.com/css2?family=Josefin+Sans:wght@400;600;700&display=swap">
<style>
:root{
  --blue:#0292cd;
  --teal:#33b8a4;
  --teal-light:#86cfc6;
  --cream:#fdf9cf;
  --red:#ec1f27;
  --ink:#1c1c1c;
  --body:#333;
  --dark:#222222;
  --footer:#131313;
  --white:#ffffff;
}
*{margin:0;padding:0;box-sizing:border-box}
html,body{width:1200px;height:3163px;overflow:hidden}
body{position:relative;font-family:"Josefin Sans",Arial,sans-serif;color:var(--body);background:var(--white)}
.abs{position:absolute}
a{color:inherit;text-decoration:none}

/* header */
.site-header{left:0;top:0;width:1200px;height:112px;background:var(--blue);color:var(--white)}
.brand{left:112px;top:34px;font-size:40px;font-weight:700;line-height:44px}
.contact-chip{top:12px;display:flex;align-items:center;gap:14px;font-size:17px;font-weight:600}
.chip-icon{width:38px;height:38px;border-radius:50%;background:var(--white);display:flex;align-items:center;justify-content:center}
.main-nav{top:66px;left:580px;display:flex;font-size:17px;font-weight:600}
.main-nav a{padding:0 11px}
.search-icon{left:1062px;top:64px}

/* hero */
.hero{left:0;top:112px;width:1200px;height:648px;overflow:hidden}
.hero-photo{left:0;top:0;width:1200px;height:648px;background:linear-gradient(90deg,#2c2f35 0%,#3b3e44 45%,#8a7b66 70%,#cfc7bb 100%)}
.hero-copy{left:112px;top:170px;color:var(--white)}
.hero-title{font-size:50px;font-weight:700;line-height:54px}
.hero-tag{font-size:34px;font-weight:400;line-height:40px}
.hero-lede{font-size:16px;line-height:27px;margin-top:16px;width:420px}
.btn{display:inline-block;background:var(--red);color:var(--white);font-weight:700;font-size:17px;text-align:center;line-height:46px;height:46px;border-radius:2px}
.hero-btn{width:152px;margin-top:22px}
.slider-dots{left:1130px;top:302px;display:flex;flex-direction:column;gap:7px}
.slider-dots span{width:12px;height:12px;border-radius:50%;background:var(--white);border:2px solid var(--white)}
.slider-dots span:first-child{background:transparent}
.hero-edge{left:0;top:600px}

/* welcome */
.welcome{left:0;top:820px;width:1200px;text-align:center;color:var(--ink)}
.welcome-pre{font-size:35px;font-weight:400;line-height:44px}
.welcome-title{font-size:44px;font-weight:700;line-height:54px;margin-top:10px}
.welcome-sub{font-size:23px;line-height:38px;width:740px;margin:22px auto 0}
.welcome-body{width:780px;margin:20px auto 0;font-size:15px;line-height:28px;color:var(--body)}
.welcome-body p{margin-bottom:8px}
.welcome-btn{width:150px;margin-top:34px}

/* benefits band */
.benefits{left:0;top:1421px;width:1200px;height:570px}
.benefits-bg{left:0;top:0}
.focus{left:112px;top:62px;width:430px;color:var(--white)}
.focus-title{font-size:25px;font-weight:700;line-height:38px}
.focus-list{list-style:none;margin-top:30px}
.focus-list li{position:relative;padding-left:30px;font-size:15px;line-height:26px;margin-bottom:14px}
.bullet{position:absolute;left:0;top:3px}
.enjoy-title{left:700px;top:62px;color:var(--white);font-size:25px;font-weight:600}
.enjoy-frame{left:702px;top:112px;width:426px;height:418px;overflow:visible}
.enjoy-list{left:732px;top:148px;width:350px;list-style:none;color:var(--white)}
.enjoy-list li{position:relative;padding-left:36px;font-size:15px;font-weight:600;line-height:28px;margin-bottom:5px}

/* organisers */
.avatar{left:156px;top:2090px;width:194px;height:194px;border-radius:50%;border:6px solid var(--blue);background:linear-gradient(160deg,#6b4b3e,#c59f83)}
.quote-badge{left:269px;top:2079px;width:52px;height:52px;border-radius:50%;background:var(--blue)}
.organisers{left:394px;top:2098px;width:680px}
.organisers-title{font-size:43px;font-weight:700;color:var(--ink);line-height:52px}
.organisers-text{font-size:15.5px;line-height:25.5px;margin-top:12px;color:var(--body);width:676px}
.organiser-name{font-size:20px;font-weight:700;color:var(--red);margin-top:22px}
.organiser-source{font-size:13px;color:#777;margin-top:8px}
.review-dots{left:226px;top:2326px;display:flex;gap:9px}
.review-dots span{width:13px;height:13px;border-radius:50%;background:#777}
.review-dots span:first-child{background:transparent;border:2px solid #555}

/* contact */
.contact-edge{left:0;top:2430px}
.contact{left:0;top:2541px;width:1200px;height:622px;background:var(--footer);color:var(--white)}
.contact-title{left:0;top:44px;width:1200px;text-align:center;font-size:41px;font-weight:700}
.map{left:202px;top:154px;width:462px;height:281px;background:linear-gradient(135deg,#e9ece4,#d7e2cf 60%,#e6e3d8)}
.contact-row{left:708px;display:flex;align-items:center;gap:22px;font-size:20px;font-weight:600;line-height:32px}
.ring{width:58px;height:58px;border-radius:50%;border:3px solid var(--red);display:flex;align-items:center;justify-content:center;flex:none}
.footer-nav{left:0;top:511px;width:1200px;display:flex;justify-content:center;gap:30px;font-size:17px;font-weight:600}
.copyright{left:0;top:558px;width:1200px;text-align:center;font-size:16px;font-weight:600}
</style>
</head>
<body>

<header class="site-header abs">
  <div class="brand abs">Makers' Hollow</div>
  <div class="contact-chip abs" style="left:648px">
    <span class="chip-icon"><svg width="20" height="16" viewBox="0 0 20 16" fill="none" stroke="#0292cd" stroke-width="2"><rect x="1" y="1" width="18" height="14" rx="1"/><path d="M1 2l9 7 9-7"/></svg></span>
    info@makershollow.co.uk
  </div>
  <div class="contact-chip abs" style="left:920px">
    <span class="chip-icon"><svg width="20" height="20" viewBox="0 0 24 24" fill="none" stroke="#0292cd" stroke-width="2"><path d="M22 16.9v3a2 2 0 0 1-2.2 2 19.8 19.8 0 0 1-8.6-3.1 19.5 19.5 0 0 1-6-6A19.8 19.8 0 0 1 2.1 4.2 2 2 0 0 1 4.1 2h3a2 2 0 0 1 2 1.7c.1 1 .4 1.9.7 2.8a2 2 0 0 1-.5 2.1L8 9.8a16 16 0 0 0 6 6l1.3-1.3a2 2 0 0 1 2.1-.4c.9.3 1.8.6 2.8.7a2 2 0 0 1 1.7 2z"/></svg></span>
    (555) 014 2870
  </div>
  <nav class="main-nav abs">
    <a href="#">Home</a><a href="#">About Us</a><a href="#">Join Us</a><a href="#">Organisers</a><a href="#">Contact Us</a>
  </nav>
  <svg class="search-icon abs" width="20" height="20" viewBox="0 0 20 20" fill="none" stroke="#fff" stroke-width="2.6"><circle cx="8" cy="8" r="6"/><path d="M12.5 12.5L18 18"/></svg>
</header>

<section class="hero abs">
  <div class="hero-photo abs" role="img" aria-label="Photo of a creative professional working thoughtfully at a laptop in a dark studio"></div>
  <div class="hero-copy abs">
    <h1 class="hero-title">Makers' Hollow</h1>
    <div class="hero-tag">focus. build. launch.</div>
    <p class="hero-lede">Lorem ipsum dolor sit amet, consectetur adipiscing elit, sed do eiusmod tempor incididunt ut.</p>
    <a class="btn hero-btn" href="#">Read More</a>
  </div>
  <div class="slider-dots abs"><span></span><span></span><span></span></div>
</section>
<svg class="abs hero-edge" width="1200" height="160" viewBox="0 0 1200 160">
  <polygon points="0,90 680,95 1200,135 1200,160 0,160" fill="#ffffff"/>
  <polygon points="0,55 680,95 0,115" fill="#e6e6e6"/>
  <polygon points="680,95 1200,50 1200,75" fill="#33b8a4"/>
  <polygon points="680,95 1200,75 1200,135" fill="#86cfc6"/>
</svg>

<section class="welcome abs">
  <div class="welcome-pre">Welcome to</div>
  <h2 class="welcome-title">Makers' Hollow</h2>
  <p class="welcome-sub">Makers’ Hollow gives you the space you need to take your side project from idea to reality.</p>
  <div class="welcome-body">
    <p>Calling all creatives! Whether you’re a software developer, a UI or UX designer, a product creator or an artworker, you’ll know only too well that great work rarely materialises when you’re in the wrong environment.</p>
    <p>Phones buzzing. Emails pinging. Video calls incoming…distractions are everywhere – and they do<br>nothing for your motivation.</p>
    <p>So, if you have a seed of a business idea and need to reclaim some focus, the Makers’ Hollow<br>is for you. Or maybe you’ve created a product, sought a patent and you’re<br>ready – and raring – to go.</p>
  </div>
  <a class="btn welcome-btn" href="#">Read More</a>
</section>

<section class="benefits abs">
  <svg class="benefits-bg abs" width="1200" height="570" viewBox="0 0 1200 570">
    <rect width="1200" height="570" fill="#222222"/>
    <polygon points="0,0 692,0 574,570 0,570" fill="#0292cd"/>
  </svg>
  <div class="focus abs">
    <h3 class="focus-title">With three days of focused work, it’s a place for you iron out the details of your business idea away from the distractions of the city</h3>
    <ul class="focus-list">
      <li><svg class="bullet" width="18" height="18" viewBox="0 0 18 18" fill="none" stroke="#fff" stroke-width="1.5"><circle cx="9" cy="9" r="7.5"/><path d="M7.5 5.5L11 9l-3.5 3.5"/></svg>Whatever stage your side hustle’s at, we’re here to help it thrive. Our warm and friendly Retreat is just that: a place to create, connect and collaborate with likeminded folks. Oh, and there’s yoga, meditation, healthy meals and snacks, and all the feedback you need to power on</li>
      <li><svg class="bullet" width="18" height="18" viewBox="0 0 18 18" fill="none" stroke="#fff" stroke-width="1.5"><circle cx="9" cy="9" r="7.5"/><path d="M7.5 5.5L11 9l-3.5 3.5"/></svg>And while you’re busy getting your side project off the ground, we’ll rustle up three healthy meals each day so that you don’t have to worry about cooking. We’ll even make sure you have a steady supply of healthy, low-sugar snacks to help fuel all those bright ideas.</li>
    </ul>
  </div>
  <h3 class="enjoy-title abs">Join the Retreat and enjoy:</h3>
  <svg class="enjoy-frame abs" width="426" height="418" viewBox="0 0 426 418" fill="none">
    <path d="M380 2H424V416H96M40 416H2V2H340" stroke="#fff" stroke-width="3"/>
    <g fill="#fff">
      <path d="M346 -12h13v12c0 8-4 13-11 15l-2-4c4-2 6-5 6-9h-6z"/>
      <path d="M364 -12h13v12c0 8-4 13-11 15l-2-4c4-2 6-5 6-9h-6z"/>
      <path d="M90 430h-13v-12c0-8 4-13 11-15l2 4c-4 2-6 5-6 9h6z"/>
      <path d="M72 430h-13v-12c0-8 4-13 11-15l2 4c-4 2-6 5-6 9h6z"/>
    </g>
  </svg>
  <ul class="enjoy-list abs">
    <li><svg class="bullet" width="18" height="18" viewBox="0 0 18 18" fill="none" stroke="#fff" stroke-width="1.5"><circle cx="9" cy="9" r="7.5"/><path d="M7.5 5.5L11 9l-3.5 3.5"/></svg>Three, full days of distraction-free work</li>
    <li><svg class="bullet" width="18" height="18" viewBox="0 0 18 18" fill="none" stroke="#fff" stroke-width="1.5"><circle cx="9" cy="9" r="7.5"/><path d="M7.5 5.5L11 9l-3.5 3.5"/></svg>A chance to hone your side project away from the office</li>
    <li><svg class="bullet" width="18" height="18" viewBox="0 0 18 18" fill="none" stroke="#fff" stroke-width="1.5"><circle cx="9" cy="9" r="7.5"/><path d="M7.5 5.5L11 9l-3.5 3.5"/></svg>The opportunity to collaborate with likeminded creatives</li>
    <li><svg class="bullet" width="18" height="18" viewBox="0 0 18 18" fill="none" stroke="#fff" stroke-width="1.5"><circle cx="9" cy="9" r="7.5"/><path d="M7.5 5.5L11 9l-3.5 3.5"/></svg>Good, honest feedback and insight from fellow attendees</li>
    <li><svg class="bullet" width="18" height="18" viewBox="0 0 18 18" fill="none" stroke="#fff" stroke-width="1.5"><circle cx="9" cy="9" r="7.5"/><path d="M7.5 5.5L11 9l-3.5 3.5"/></svg>Daily yoga and meditation to help fuel your ideas</li>
    <li><svg class="bullet" width="18" height="18" viewBox="0 0 18 18" fill="none" stroke="#fff" stroke-width="1.5"><circle cx="9" cy="9" r="7.5"/><path d="M7.5 5.5L11 9l-3.5 3.5"/></svg>Three, nutritious and delicious meals a day</li>
    <li><svg class="bullet" width="18" height="18" viewBox="0 0 18 18" fill="none" stroke="#fff" stroke-width="1.5"><circle cx="9" cy="9" r="7.5"/><path d="M7.5 5.5L11 9l-3.5 3.5"/></svg>Healthy, low-sugar snacks to get you through the day</li>
  </ul>
</section>

<div class="avatar abs" role="img" aria-label="Portrait of the retreat organiser"></div>
<div class="quote-badge abs">
  <svg width="52" height="52" viewBox="0 0 52 52" fill="#fff"><path d="M15 30v-5c0-5 3-8 7-9l1 3c-2 1-4 3-4 5h4v6z"/><path d="M27 30v-5c0-5 3-8 7-9l1 3c-2 1-4 3-4 5h4v6z"/></svg>
</div>
<section class="organisers abs">
  <h2 class="organisers-title">Meet Your Retreat Organisers</h2>
  <p class="organisers-text">An internationally-certified yoga teacher, Mara loves connecting with people and discovering how she can help them get the best out of their day – and their work. Giving attendees the time to enjoy some self-care in the form of a spot of gentle yoga, animal lover Mara will help you unleash those ideas!</p>
  <div class="organiser-name">Mara Lindqvist</div>
  <div class="organiser-source">via Snapwall reviews</div>
</section>
<div class="review-dots abs"><span></span><span></span><span></span></div>

<svg class="contact-edge abs" width="1200" height="112" viewBox="0 0 1200 112">
  <polygon points="0,6 540,52 0,52" fill="#86cfc6"/>
  <polygon points="0,52 540,52 0,111" fill="#33b8a4"/>
  <polygon points="0,112 540,52 1200,6 1200,112" fill="#131313"/>
</svg>

<footer class="contact abs">
  <h2 class="contact-title abs">Contact Us</h2>
  <div class="map abs" role="img" aria-label="Road map showing the retreat location"></div>

  <div class="contact-row abs" style="top:168px">
    <span class="ring"><svg width="22" height="28" viewBox="0 0 22 28" fill="#fff"><path d="M11 0a11 11 0 0 0-11 11c0 8 11 17 11 17s11-9 11-17A11 11 0 0 0 11 0zm0 15a4 4 0 1 1 0-8 4 4 0 0 1 0 8z"/></svg></span>
    <span>418 Alder Mill Road<br>Millbrook, PA 19022 USA</span>
  </div>
  <div class="contact-row abs" style="top:267px">
    <span class="ring"><svg width="24" height="24" viewBox="0 0 24 24" fill="none" stroke="#fff" stroke-width="2"><path d="M22 16.9v3a2 2 0 0 1-2.2 2 19.8 19.8 0 0 1-8.6-3.1 19.5 19.5 0 0 1-6-6A19.8 19.8 0 0 1 2.1 4.2 2 2 0 0 1 4.1 2h3a2 2 0 0 1 2 1.7c.1 1 .4 1.9.7 2.8a2 2 0 0 1-.5 2.1L8 9.8a16 16 0 0 0 6 6l1.3-1.3a2 2 0 0 1 2.1-.4c.9.3 1.8.6 2.8.7a2 2 0 0 1 1.7 2z"/></svg></span>
    <span>(555) 014 2870</span>
  </div>
  <div class="contact-row abs" style="top:357px">
    <span class="ring"><svg width="26" height="20" viewBox="0 0 26 20" fill="none" stroke="#fff" stroke-width="2"><rect x="1" y="1" width="24" height="18" rx="1"/><path d="M1 2l12 9 12-9M1 19l9-8M25 19l-9-8"/></svg></span>
    <span>info@makershollow.co.uk</span>
  </div>

  <nav class="footer-nav abs">
    <a href="#">Home</a><a href="#">About Us</a><a href="#">Join Us</a><a href="#">User Reviews</a><a href="#">Contact Us</a>
  </nav>
  <p class="copyright abs">© 2019 Copyrights | All Rights Reserved</p>
</footer>

</body>
</html>
```